wordpress website Carla Winfield, Author, Speaker and Coach

Need a wordpress blogging website for author/speaker/coach.
I have paid for hosting on nestparrot.
I am currently writing a book - Launchpad to Campus - Steps and strategies to prepare you to thrive in college and beyond. Eventually, I will have an Academic/Life Coaching program targeting high school and college students. This website's purpose is to build my email list. I can offer the following reports as incentive for email sign-up:
1. Six Habits That Get Your Teen Through University On Schedule and Debt-Light
2. Surprising Routes to Fund Your Degree
3. SAT/ACT vocabulary word of the day

facebook page: https://www.facebook.com/Carla-Winfield-AcademicLife-Coach-918273645501928/

I would like to have these pages:

1. Home or About page

High school is becoming more and more stressful for students. Not only are they taking more AP classes than ever before, and often spending $1,000’s on SAT/ACT prep programs, most are NOT prepared for success in college. Only 19% of students are graduating from college within 4 years and only 56% are graduating within 6 years. With the cost of higher education skyrocketing, each extra year of school can costs families $40,000 - $60,000 when you factor in living expenses. Then, when students do graduate, they are often underemployed.

Carla's approach is whole person oriented. Her programs help students learn life skills in addition to the study, time management skills, etc. offered by most academic coaching programs. Our program addresses all of the major causes of failure to graduate within 4 years, and is based on sound educational research. Carla's program initially provides the daily interaction needed to successfully change behaviors and seat new success habits, unlike many programs in which students interact with coaches only once a week.
Bio
Carla Winfield is a certified teacher and holds advanced certification in academic coaching and tutoring. She also is a certified trainer in the Morris Tellwright Achievement Keys. She has three successful adult children, and helped them overcome learning differences and thrive.

2. Blog

3. Contact - Include form (I split time between USA and Saudi Arabia, so I will call or email people back, but don't want to leave a phone number)
info@carlawinfield.example

4. Store – 1 book for now
Launchpad to Campus
Steps and strategies to prepare you to thrive in college and beyond
Available 12/01/2017
I could make a preview chapter available for download

5. Speaking
Carla Winfield is available for keynote addresses and half-day, full day or multi-day workshops. I will develop details later

6.Coaching programs
I will develop details later

Target Market(s)

high school students who are college bound and their parents

Number of Pages Required

5+ page

Font styles to use
Sans Serif

Colors

Designer to choose colors to be used in the design.

Requirements
Nice to have
• integration with post finch for contact management

```html
<!DOCTYPE html>
<html lang="en">
<head>
<meta charset="utf-8">
<title>Carla Winfield – Author, Speaker and Coach</title>
<link rel="stylesheet" href="https://fonts.googleapis.com/css2?family=Lato:ital,wght@0,400;0,700;0,900;1,700&display=swap">
<style>
:root{
  --green:#8cc63f;
  --green-dark:#1b8a4a;
  --lavender:#8f8dd0;
  --navy:#2c3a4c;
  --ink:#222;
  --muted:#666;
  --light:#f4f4f4;
  --white:#fff;
}
*{box-sizing:border-box;margin:0;padding:0}
html,body{width:1200px;height:4423px;overflow:hidden}
body{font-family:'Lato',sans-serif;color:var(--ink);background:var(--white);position:relative}
.section{position:absolute;left:0;width:1200px;overflow:hidden}
.abs{position:absolute}
.btn{position:absolute;display:flex;align-items:center;justify-content:center;font-size:13px;font-weight:700;letter-spacing:.5px;text-transform:uppercase;color:var(--white)}
.btn-green{background:var(--green)}
.btn-lav{background:var(--lavender)}
.btn-outline{border:2px solid var(--white);background:transparent}
.ph{position:absolute}

/* header */
.site-header{top:0;height:74px;background:var(--white)}
.brand{left:162px;top:18px;display:flex;align-items:center;gap:10px;font-size:30px;font-weight:700;color:var(--ink)}
.brand-dot{width:34px;height:34px;border-radius:50%;background:var(--green)}
.main-nav{right:162px;top:20px;display:flex;align-items:center;gap:22px;font-size:13px;font-weight:700}
.nav-home{width:34px;height:34px;background:var(--green);display:flex;align-items:center;justify-content:center}
.nav-search{width:30px;height:30px;border:1px solid #ccc;display:flex;align-items:center;justify-content:center}

/* hero */
.hero{top:74px;height:471px;background:linear-gradient(180deg,#4a4036,#2c2621 60%,#3a3129)}
.hero-title{left:162px;top:150px;font-size:30px;font-weight:900;color:var(--white);letter-spacing:.5px}
.hero-sub{left:162px;top:200px;font-size:18px;font-weight:700;color:var(--white);line-height:1.4}
.hero-arrow{top:210px}
.book-cover{left:760px;top:44px;width:257px;height:369px;background:linear-gradient(135deg,#6b6bc4,#d94ca3 55%,#f6c233);box-shadow:8px 8px 0 #222}

/* welcome */
.welcome{top:545px;height:404px}
.welcome-video{left:162px;top:65px;width:413px;height:260px;background:linear-gradient(135deg,#3a3a3a,#b98a6a 60%,#e6c9a0)}
.play{left:334px;top:165px;width:64px;height:44px;border-radius:10px;background:#e52d27;display:flex;align-items:center;justify-content:center}
.welcome-title{left:610px;top:70px;font-size:30px;font-weight:400}
.welcome-title b{font-weight:900}
.welcome-text{left:610px;top:118px;width:428px;font-size:13px;line-height:1.6;color:var(--muted)}
.welcome-text p{margin-bottom:10px}

/* limits band */
.limits{top:949px;height:304px;background:var(--green)}
.limits-photo{left:133px;top:20px;width:324px;height:284px;background:linear-gradient(135deg,#e8d5c4,#3b6fb0 50%,#c52f2f)}
.limits-title{left:486px;top:70px;font-size:28px;font-weight:700;font-style:italic;color:var(--white)}
.limits-text{left:486px;top:118px;width:560px;font-size:13px;line-height:1.6;color:var(--white)}

/* programs */
.programs{top:1253px;height:442px}
.program{top:74px;width:413px;height:295px}
.program-photo{left:0;top:0;width:413px;height:295px}
.program-bar{left:0;bottom:0;width:413px;height:56px;background:rgba(140,198,63,.92);display:flex;align-items:center;justify-content:space-between;padding:0 20px}
.program-bar h3{font-size:17px;font-weight:700;color:var(--white)}
.program-bar span{border:1px solid var(--white);color:var(--white);font-size:11px;font-weight:700;padding:5px 10px}

/* shop */
.shop{top:1695px;height:502px}
.shop-panel{left:0;top:0;width:598px;height:502px;background:var(--lavender)}
.shop-title{left:162px;top:168px;font-size:28px;font-weight:700;color:var(--white)}
.shop-text{left:162px;top:212px;font-size:12px;line-height:1.6;color:var(--white)}
.chapter{width:301px;height:251px}
.chapter-photo{left:0;top:0;width:301px;height:251px}
.chapter-cap{left:0;bottom:0;width:301px;height:30px;background:rgba(0,0,0,.7);color:var(--white);font-size:12px;font-weight:700;display:flex;align-items:center;justify-content:center}

/* blog */
.blog{top:2197px;height:472px}
.section-title{width:1200px;text-align:center;font-size:32px;font-weight:900}
.blog-card{background:var(--light);box-shadow:0 2px 6px rgba(0,0,0,.08)}
.date{width:72px;height:60px;background:var(--white);font-size:12px;font-weight:700;text-align:center;padding-top:8px;line-height:1.4}
.card-title{font-size:17px;font-weight:700;line-height:1.3}
.card-meta{font-size:11px;color:var(--muted);line-height:1.6}
.read{font-size:11px;font-weight:700;color:var(--green-dark)}

/* newsletter */
.newsletter{top:2678px;height:286px;background:var(--green-dark)}
.news-title{width:1200px;text-align:center;top:70px;font-size:28px;color:var(--white)}
.news-sub{width:1200px;text-align:center;top:116px;font-size:13px;font-style:italic;font-weight:700;color:var(--white)}
.news-input{left:298px;top:165px;width:395px;height:40px;background:var(--white);font-size:13px;color:#999;padding:11px 14px}

/* happy students */
.happy{top:2964px;height:491px}
.happy-text{left:162px;top:206px;width:472px;font-size:12px;line-height:1.6;color:var(--muted)}
.happy-name{left:162px;top:388px;font-size:16px;font-weight:700;color:var(--green-dark);line-height:1.2}
.happy-role{left:162px;top:410px;font-size:11px;color:var(--muted);line-height:1.3}
.happy-bars{left:162px;top:434px}
.happy-photo{left:643px;top:118px;width:522px;height:368px;background:linear-gradient(135deg,#f3e8dc,#e0a57a 50%,#c94a4a)}

/* contact */
.map{top:3455px;height:497px;background:linear-gradient(180deg,#e9e9e9,#dcdcdc)}
.contact-dark{top:3952px;height:383px;background:var(--navy)}
.contact-box{left:162px;top:3828px;width:876px;height:339px;background:var(--green);position:absolute}
.contact-box h2{position:absolute;width:876px;text-align:center;top:32px;font-size:26px;font-weight:900;color:var(--white)}
.field{position:absolute;background:var(--white);font-size:12px;color:#888;padding:12px}
.submit{left:343px;top:274px;width:190px;height:38px;background:#2a2a2a}
.info{top:4232px;display:flex;align-items:center;gap:18px;color:var(--white);font-size:12px;line-height:1.5}
.info-icon{width:50px;height:50px;border-radius:50%;border:2px solid var(--white);display:flex;align-items:center;justify-content:center}

/* footer */
.site-footer{top:4335px;height:88px;background:#151515}
.copyright{left:162px;top:36px;font-size:12px;color:#bbb}
.social{right:162px;top:30px;display:flex;gap:10px}
.social span{width:28px;height:28px;border-radius:50%;background:var(--green)}
</style>
</head>
<body>

<header class="section site-header">
  <div class="abs brand"><span class="brand-dot"></span>Carla Winfield</div>
  <nav class="abs main-nav">
    <span class="nav-home"><svg width="16" height="16" viewBox="0 0 16 16"><path d="M8 2 1 8h2v6h4v-4h2v4h4V8h2z" fill="#fff"/></svg></span>
    <span>About Us</span><span>Coaching programs</span><span>Speaking</span><span>Store</span><span>Blog</span><span>Contact Us</span>
    <span class="nav-search"><svg width="12" height="12" viewBox="0 0 12 12"><circle cx="5" cy="5" r="3.5" stroke="#555" stroke-width="1.5" fill="none"/><path d="M7.6 7.6 11 11" stroke="#555" stroke-width="1.5"/></svg></span>
  </nav>
</header>

<section class="section hero" role="img" aria-label="Library with bookshelves in the background">
  <svg class="abs hero-arrow" style="left:100px" width="34" height="60" viewBox="0 0 34 60"><path d="M28 4 6 30l22 26" stroke="#fff" stroke-width="5" fill="none"/></svg>
  <svg class="abs hero-arrow" style="left:1066px" width="34" height="60" viewBox="0 0 34 60"><path d="M6 4l22 26L6 56" stroke="#fff" stroke-width="5" fill="none"/></svg>
  <h1 class="abs hero-title">LEARNING ANY WHERE ANY TIME</h1>
  <p class="abs hero-sub">We Help Students Reach Theri Life Goals Faster<br>And More Efficiently.</p>
  <span class="btn btn-green" style="left:162px;top:270px;width:125px;height:38px">Buy Today!</span>
  <span class="btn btn-outline" style="left:300px;top:270px;width:130px;height:38px">Contact Now!</span>
  <div class="ph book-cover" role="img" aria-label="Life Coaching Program book cover with author portrait"></div>
</section>

<section class="section welcome">
  <div class="ph welcome-video" role="img" aria-label="Welcome video still of Carla Winfield"></div>
  <div class="abs play"><svg width="18" height="20" viewBox="0 0 18 20"><path d="M0 0l18 10L0 20z" fill="#fff"/></svg></div>
  <h2 class="abs welcome-title">WELCOMR TO <b>CARLA WINFIELD</b></h2>
  <div class="abs welcome-text">
    <p>Carla Winfield is a certified teacher and holds advanced certification in academic coaching and tutoring. She also is a certified trainer in the Morris Tellwright Achievement Keys. She has three successful adult children, and helped them overcome learning differences and thrive.</p>
    <p>Carla's approach is whole person oriented. Her programs help students learn life skills in addition to the study, time management skills, etc. offered by most academic coaching programs.</p>
  </div>
  <span class="btn btn-lav" style="left:610px;top:297px;width:118px;height:26px;font-size:11px">Read More</span>
</section>

<section class="section limits">
  <div class="ph limits-photo" role="img" aria-label="Two smiling students carrying books and backpacks"></div>
  <h2 class="abs limits-title">LEARNING WITHOUT LIMITS</h2>
  <p class="abs limits-text">It is a long established fact that a reader will be distracted by the readable content of a page when looking at its layout.</p>
  <span class="btn btn-lav" style="left:486px;top:172px;width:130px;height:38px">Get Start Now</span>
  <span class="btn btn-lav" style="left:632px;top:172px;width:110px;height:38px">Shop Now</span>
</section>

<section class="section programs">
  <div class="abs program" style="left:162px">
    <div class="ph program-photo" role="img" aria-label="Speaker presenting to an audience with a projector screen" style="background:linear-gradient(135deg,#2b2b2b,#8a7a6a 55%,#d9d0c2)"></div>
    <div class="abs program-bar"><h3>SPEAKING PROGRAMS</h3><span>READ MORE</span></div>
  </div>
  <div class="abs program" style="left:625px">
    <div class="ph program-photo" role="img" aria-label="Coach with a group of people in a classroom" style="background:linear-gradient(135deg,#f0ede8,#b9a999 50%,#3a3a3a)"></div>
    <div class="abs program-bar"><h3>COACHING PROGRAMS</h3><span>READ MORE</span></div>
  </div>
</section>

<section class="section shop">
  <div class="ph shop-panel"></div>
  <h2 class="abs shop-title">SHOP</h2>
  <p class="abs shop-text">Launchpad to Campus<br>Steps and strategies to prepare you to thrive in college and beyond<br>Available 12/01/2017</p>
  <span class="btn btn-green" style="left:162px;top:300px;width:125px;height:34px;font-size:11px">View Shop</span>
  <span class="btn btn-green" style="left:300px;top:300px;width:230px;height:34px;font-size:11px">Download Preview Chapter</span>
  <div class="abs chapter" style="left:598px;top:0"><div class="ph chapter-photo" role="img" aria-label="Student holding books outdoors" style="background:linear-gradient(135deg,#a5543c,#c89a7c 60%,#3d2e2a)"></div><div class="abs chapter-cap">1 Chapter Available</div></div>
  <div class="abs chapter" style="left:899px;top:0"><div class="ph chapter-photo" role="img" aria-label="Student with notebooks" style="background:linear-gradient(135deg,#e9e4de,#9d8574 60%,#2e2a2a)"></div><div class="abs chapter-cap">2 Chapter Available</div></div>
  <div class="abs chapter" style="left:598px;top:251px"><div class="ph chapter-photo" role="img" aria-label="Group of cheerful students" style="background:linear-gradient(135deg,#d9b28f,#c2493f 55%,#3b5c8f)"></div><div class="abs chapter-cap">3 Chapter Available</div></div>
  <div class="abs chapter" style="left:899px;top:251px"><div class="ph chapter-photo" role="img" aria-label="Students studying together at a table" style="background:linear-gradient(135deg,#d8cfc4,#8b7b6b 55%,#44576b)"></div><div class="abs chapter-cap">4 Chapter Available</div></div>
</section>

<section class="section blog">
  <h2 class="abs section-title" style="top:50px">LETEST BLOG</h2>
  <svg class="abs" style="left:118px;top:245px" width="18" height="34" viewBox="0 0 18 34"><path d="M15 2 3 17l12 15" stroke="#555" stroke-width="3" fill="none"/></svg>
  <svg class="abs" style="left:1064px;top:245px" width="18" height="34" viewBox="0 0 18 34"><path d="M3 2l12 15L3 32" stroke="#555" stroke-width="3" fill="none"/></svg>
  <article class="abs blog-card" style="left:171px;top:123px;width:492px;height:274px">
    <h3 class="abs card-title" style="left:22px;top:22px;width:220px">Lorem ipsum dolor sit amet, consectetuer</h3>
    <p class="abs card-meta" style="left:22px;top:85px">Posted by : Admin</p>
    <p class="abs card-meta" style="left:22px;top:120px;width:215px">Since moving to digital photos years back, I have developed a happy finger which is taken to taking pictures, so many files sit in folders adipiscing elit, sed diam nonummy nibh.</p>
    <span class="abs read" style="left:22px;top:228px">Read More ➞</span>
    <div class="ph" role="img" aria-label="Student writing in a notebook" style="left:260px;top:0;width:232px;height:274px;background:linear-gradient(135deg,#efe6d8,#c9a57f 55%,#6b4c36)"></div>
    <div class="abs date" style="left:262px;top:12px">30 JUN<br>2017</div>
  </article>
  <article class="abs blog-card" style="left:731px;top:123px;width:295px;height:127px">
    <div class="ph" role="img" aria-label="Group of students" style="left:0;top:0;width:130px;height:127px;background:linear-gradient(135deg,#d5b08d,#b5443a 60%,#3f5b8a)"></div>
    <div class="abs date" style="left:0;top:10px;width:60px;height:50px;padding-top:5px">29 JUN<br>2017</div>
    <h3 class="abs card-title" style="left:142px;top:8px;width:145px;font-size:12px">Lorem ipsum dolor sit amet, consectetuer</h3>
    <p class="abs card-meta" style="left:142px;top:45px;width:145px;font-size:10px">Since moving to digital photos years back...</p>
    <span class="abs read" style="left:142px;top:95px;font-size:10px">Read More ➞</span>
  </article>
  <article class="abs blog-card" style="left:731px;top:270px;width:295px;height:127px">
    <div class="ph" role="img" aria-label="Students studying in a library" style="left:0;top:0;width:130px;height:127px;background:linear-gradient(135deg,#e2dbd0,#8d7b69 55%,#3b4658)"></div>
    <div class="abs date" style="left:0;top:10px;width:60px;height:50px;padding-top:5px">28 JUN<br>2017</div>
    <h3 class="abs card-title" style="left:142px;top:8px;width:145px;font-size:12px">Lorem ipsum dolor sit amet, consectetuer</h3>
    <p class="abs card-meta" style="left:142px;top:45px;width:145px;font-size:10px">Since moving to digital photos years back...</p>
    <span class="abs read" style="left:142px;top:95px;font-size:10px">Read More ➞</span>
  </article>
</section>

<section class="section newsletter">
  <h2 class="abs news-title">Subscribe To Our Newsletter</h2>
  <p class="abs news-sub">Sign Up To Receive Email Updates About Courses</p>
  <div class="abs news-input">Enter your email</div>
  <span class="btn btn-green" style="left:708px;top:165px;width:191px;height:40px">Subscribe</span>
</section>

<section class="section happy">
  <h2 class="abs section-title" style="top:60px">OUR HAPPY STUDENTS</h2>
  <p class="abs happy-text">Lorem Ipsum is simply dummy text of the printing and typesetting industry. Lorem Ipsum has been the industry's standard dummy text ever since the 1500s, when an unknown printer took a galley of type and scrambled it to make a type specimen book. It has survived not only five centuries, but also the leap into electronic typesetting, remaining essentially unchanged. It was popularised in the 1960s with the release of sheets containing Lorem Ipsum passages, and more recently with desktop publishing software.</p>
  <p class="abs happy-name">Mr Lorem Ipsum</p>
  <p class="abs happy-role">Creative Manager</p>
  <svg class="abs happy-bars" width="80" height="4"><rect width="22" height="3" fill="#8cc63f"/><rect x="28" width="22" height="3" fill="#8cc63f"/><rect x="56" width="22" height="3" fill="#ccc"/></svg>
  <div class="ph happy-photo" role="img" aria-label="Group of cheering, jumping students"></div>
</section>

<div class="section map" role="img" aria-label="Map of the central United States"></div>
<div class="section contact-dark"></div>

<section class="contact-box">
  <h2>GET TOUCH WITH ME</h2>
  <div class="field" style="left:112px;top:97px;width:257px;height:40px">Name*</div>
  <div class="field" style="left:383px;top:97px;width:378px;height:40px">Subject*</div>
  <div class="field" style="left:112px;top:153px;width:257px;height:40px">Email*</div>
  <div class="field" style="left:383px;top:153px;width:378px;height:96px">Message</div>
  <div class="field" style="left:112px;top:209px;width:257px;height:40px">Phone*</div>
  <span class="btn submit">Submit</span>
</section>

<div class="abs info" style="left:184px">
  <span class="info-icon"><svg width="18" height="24" viewBox="0 0 18 24"><path d="M9 1a8 8 0 0 0-8 8c0 6 8 14 8 14s8-8 8-14a8 8 0 0 0-8-8z" fill="#fff"/><circle cx="9" cy="9" r="3" fill="#2c3a4c"/></svg></span>
  <span>Lorem Ipsum is simply dummy<br>text of the printing · 000000</span>
</div>
<div class="abs info" style="left:538px">
  <span class="info-icon"><svg width="22" height="16" viewBox="0 0 22 16"><rect x="1" y="1" width="20" height="14" fill="none" stroke="#fff" stroke-width="2"/><path d="M1 1l10 8 10-8" fill="none" stroke="#fff" stroke-width="2"/></svg></span>
  <span>info@carlawinfield.example<br>opportunity@carlawinfield.example</span>
</div>
<div class="abs info" style="left:854px">
  <span class="info-icon"><svg width="20" height="20" viewBox="0 0 20 20"><path d="M4 1l4 4-2 3c1 2 4 5 6 6l3-2 4 4-3 3C9 19 1 11 1 4z" fill="#fff"/></svg></span>
  <span>+1-555-0142-890<br>+1-555-0187-230</span>
</div>

<footer class="section site-footer">
  <p class="abs copyright">© 2017 Carla Winfield. All Rights Reserved</p>
  <div class="abs social"><span></span><span></span><span></span><span></span></div>
</footer>

</body>
</html>
```